Redesign of business card for Cedar Ridge Mechanical

We are looking for a new design for our business cards for Cedar Ridge Mechanical. We are a plumbing & HVAC construction company, operating on the West Coast of Canada and USA. Logo attached.
Industry/Entity Type
Construction - Plumbing & HVAC
Contact Information for Business Card
Name, address, phone numbers, email, website address
Look and feel
Each slider illustrates characteristics of the customer's brand and the style your logo design should communicate.

```html
<!DOCTYPE html>
<html lang="en">
<head>
<meta charset="utf-8">
<title>Cedar Ridge Mechanical – Business Card</title>
<link href="https://fonts.googleapis.com/css2?family=Montserrat:wght@400;500;700&family=Oswald:wght@500&display=swap" rel="stylesheet">
<style>
  :root {
    --stage: #1f1f1f;
    --card-black: #141414;
    --card-white: #ffffff;
    --ink: #151515;
    --grey: #9a9a9a;
    --pattern: #262626;
  }
  html, body { margin: 0; padding: 0; }
  body {
    width: 1200px; height: 801px; overflow: hidden;
    background: var(--stage);
    font-family: "Montserrat", sans-serif;
    position: relative;
  }
  .card {
    position: absolute; width: 530px; height: 303px;
    border-radius: 22px; overflow: hidden;
    box-shadow: 0 18px 40px rgba(0,0,0,.55);
  }
  .card--front { left: 45px; top: 249px; background: var(--card-white); }
  .card--back { left: 625px; top: 249px; background: var(--card-black); }

  .band { position: absolute; inset: 0; }

  .brand {
    position: absolute; left: 0; right: 40px; top: 48px;
    display: flex; align-items: center; justify-content: center; gap: 14px;
  }
  .brand__mark { width: 34px; height: 34px; border: 5px solid var(--ink); box-sizing: border-box; }
  .brand__name {
    font-family: "Oswald", sans-serif; font-weight: 500; font-size: 26px;
    letter-spacing: 1px; text-transform: uppercase; color: var(--ink);
  }

  .person { position: absolute; left: 30px; top: 163px; width: 194px; color: #fff; text-align: right; }
  .person__name { font-weight: 700; font-size: 19px; letter-spacing: .5px; }
  .person__title { font-size: 14px; margin-top: 2px; }
  .divider { position: absolute; left: 238px; top: 154px; width: 1px; height: 70px; background: #8a8a8a; }
  .contacts { position: absolute; left: 252px; top: 149px; color: #fff; font-size: 14px; line-height: 26px; }
  .contacts ul { margin: 0; padding: 0; }
  .contacts li { list-style: none; display: flex; align-items: center; gap: 8px; white-space: nowrap; }
  .contacts svg { width: 12px; height: 12px; fill: #fff; flex: none; }
  .address { position: absolute; left: 0; width: 440px; top: 256px; text-align: center; font-size: 15px; color: var(--ink); }

  .back-texture { position: absolute; inset: 0; background: linear-gradient(135deg, var(--pattern), var(--card-black)); }
  .back-brand {
    position: absolute; inset: 0;
    display: flex; align-items: center; justify-content: center; gap: 18px;
  }
  .back-brand__mark { width: 54px; height: 54px; border: 7px solid #fff; box-sizing: border-box; }
  .back-brand__name {
    font-family: "Oswald", sans-serif; font-weight: 500; font-size: 34px;
    letter-spacing: 1px; text-transform: uppercase; color: #fff;
  }
</style>
</head>
<body>
  <section class="card card--front">
    <svg class="band" viewBox="0 0 530 303" aria-hidden="true">
      <path d="M0 140 H410 Q495 140 530 92 V303 H485 Q475 240 405 240 H0 Z" fill="#141414"/>
      <path d="M0 133 H60" stroke="#141414" stroke-width="5"/>
      <path d="M440 130 Q500 124 530 82" stroke="#9a9a9a" stroke-width="6" fill="none"/>
      <path d="M0 248 H30" stroke="#9a9a9a" stroke-width="6"/>
    </svg>
    <div class="brand">
      <span class="brand__mark"></span>
      <span class="brand__name">Cedar Ridge Mechanical</span>
    </div>
    <div class="person">
      <div class="person__name">MARCUS HALE</div>
      <div class="person__title">Manager</div>
    </div>
    <div class="divider"></div>
    <div class="contacts">
      <ul>
        <li><svg viewBox="0 0 24 24"><path d="M6.6 10.8a15 15 0 0 0 6.6 6.6l2.2-2.2c.3-.3.7-.4 1-.2 1.1.4 2.3.6 3.6.6.6 0 1 .4 1 1V20c0 .6-.4 1-1 1A17 17 0 0 1 3 4c0-.6.4-1 1-1h3.5c.6 0 1 .4 1 1 0 1.3.2 2.5.6 3.6.1.3 0 .7-.2 1z"/></svg>604-555-0187</li>
        <li><svg viewBox="0 0 24 24"><path d="M2 5h20v14H2zm2 2v.5l8 5 8-5V7z"/></svg>office@cedarridgemech.com</li>
        <li><svg viewBox="0 0 24 24"><circle cx="12" cy="12" r="10"/></svg>www.cedarridgemech.com</li>
      </ul>
    </div>
    <div class="address">Your address, city, state, ZIP 0000</div>
  </section>

  <section class="card card--back">
    <div class="back-texture" role="img" aria-label="Faint repeating brand pattern in dark grey"></div>
    <div class="back-brand">
      <span class="back-brand__mark"></span>
      <span class="back-brand__name">Cedar Ridge Mechanical</span>
    </div>
  </section>
</body>
</html>
```